Casino with the 'highest winning percentage' needs a stationery design

This is for a casino in Colombo, Sri Lanka and we need a stationery design for business card, letter head and envelope.

Should be very professional, simple and elegant without fancy fonts

Reason: Not fully satisfied with the designs. Need more designs.

Business

• 1. card deck symbol 'CLUBS' in red, or black

2. name in BLOCK CAPITAL LETTERS

3. Preferred font colours are black, white or red

4. Prefer 'professional /elegant' fonts
• SHOULD NOT HAVE ANY OTHER SYMBOL EXCEPT 'CLUBS'

DO NOT PREFER ITALIC FONTS

```html
<!DOCTYPE html>
<html lang="en">
<head>
<meta charset="utf-8">
<title>Carrow's Entertainment – Envelope Stationery</title>
<link rel="stylesheet" href="https://fonts.googleapis.com/css2?family=Arimo:wght@400;700&display=swap">
<style>
  :root {
    --backdrop: #ececec;
    --paper: #f7f7f7;
    --paper-edge: #e2e2e2;
    --club-red: #9b1b25;
    --club-red-deep: #871720;
    --ink: #3a3a3a;
    --ink-soft: #555555;
    --ghost: #c9c9c9;
    --petal-light: #dcb1b6;
    --petal-mid: #c5868d;
  }

  * { margin: 0; padding: 0; box-sizing: border-box; }

  html, body {
    width: 1200px;
    height: 892px;
    overflow: hidden;
    background: var(--backdrop);
    font-family: "Arimo", Arial, sans-serif;
  }

  .canvas {
    position: relative;
    width: 1200px;
    height: 892px;
  }

  .envelope {
    position: absolute;
    width: 760px;
    height: 380px;
    background: var(--paper);
    border: 1px solid var(--paper-edge);
    box-shadow: 0 6px 18px rgba(0, 0, 0, 0.10);
    overflow: hidden;
  }

  /* Front of the envelope */
  .envelope--front { left: 60px; top: 60px; }

  .brand {
    position: absolute;
    left: 56px;
    top: 46px;
    display: flex;
    align-items: flex-start;
    gap: 12px;
    color: var(--ink);
  }

  .brand__dot {
    width: 18px;
    height: 18px;
    border-radius: 50%;
    background: var(--club-red);
    margin-top: 3px;
  }

  .brand__name {
    font-size: 20px;
    font-weight: 700;
    letter-spacing: 2px;
    line-height: 1.25;
    text-transform: uppercase;
  }

  .brand__name span { display: block; }

  .return-address {
    position: absolute;
    left: 56px;
    top: 200px;
    font-size: 12px;
    line-height: 1.5;
    color: var(--ink-soft);
  }

  .petal-art {
    position: absolute;
    right: 0;
    bottom: 0;
    width: 430px;
    height: 200px;
    border-top-left-radius: 200px 200px;
    background: linear-gradient(160deg, var(--petal-light) 0%, var(--petal-mid) 70%);
    opacity: 0.9;
  }

  /* Back of the envelope */
  .envelope--back { left: 380px; top: 470px; }

  .flap {
    position: absolute;
    left: 0;
    top: 0;
    width: 100%;
    height: 140px;
    background: var(--club-red);
    border-bottom-left-radius: 14px;
    border-bottom-right-radius: 14px;
  }

  .flap__seal {
    position: absolute;
    left: 50%;
    top: 88px;
    width: 24px;
    height: 24px;
    margin-left: -12px;
    border-radius: 50%;
    background: var(--club-red-deep);
  }

  .back-mark {
    position: absolute;
    left: 0;
    right: 0;
    top: 226px;
    text-align: center;
    color: var(--ghost);
    font-size: 18px;
    font-weight: 700;
    letter-spacing: 2px;
    line-height: 1.3;
    text-transform: uppercase;
  }

  .back-mark span { display: block; }
</style>
</head>
<body>
<main class="canvas">

  <section class="envelope envelope--front" aria-label="Envelope front">
    <div class="brand">
      <div class="brand__dot"></div>
      <p class="brand__name"><span>Carrow's</span><span>Entertainment</span><span>Sri Lanka</span></p>
    </div>
    <address class="return-address">
      27, Harbour View Lane<br>
      Colombo 01000, Sri Lanka
    </address>
    <div class="petal-art" role="img" aria-label="Soft red curved petal decoration"></div>
  </section>

  <section class="envelope envelope--back" aria-label="Envelope back">
    <div class="flap">
      <div class="flap__seal"></div>
    </div>
    <p class="back-mark"><span>Carrow's</span><span>Entertainment</span></p>
  </section>

</main>
</body>
</html>
```